Screen design for customizable PARISH APP

I am building a customizable app for churches. I need the following screens designed:
1) Landing Screen
-- Text field to enter a code to join a organization
-- Button to register a new organization
2) Registration Screen
-- Text field to enter an organization name
-- Register button
-- Screen should indicate price/month and free trial for X days
3) Restricted (requires login) screen
4) Organization home screen
-- Dynamic menu options of the following types:
a) Contact Us/Form
b) Video List
c) Audio List
d) Documents List
e) Message/Chat Rooms
f) Map/Directions
g) Webpage

Plus permission based options:
h) Profile Settings
i) Notification Center
j) Admin Settings
k) Manage members
l) View Form Submissions

Low-fi/wireframe designs attached. No color scheme or branding has been established yet.

```html
<!DOCTYPE html>
<html lang="en">
<head>
<meta charset="utf-8">
<title>Parish App – Screen Designs</title>
<link href="https://fonts.googleapis.com/css2?family=Poppins:wght@300;400;500;600&display=swap" rel="stylesheet">
<style>
:root{
  --gold-light:#d0b063;
  --gold-dark:#ad8a4a;
  --gold-accent:#b8914c;
  --blue-top:#34599f;
  --blue-bottom:#1f3b72;
  --header-blue:#2a4d93;
  --btn-start:#135296;
  --btn-end:#0c3365;
  --navy-text:#1f3a6e;
  --grey-text:#8a8f99;
  --field-border:#c9ccd3;
  --white:#ffffff;
}
*{margin:0;padding:0;box-sizing:border-box}
html,body{width:1200px;height:1200px;overflow:hidden}
body{
  font-family:'Poppins',sans-serif;
  background:linear-gradient(160deg,var(--gold-light) 0%,#c6a35a 50%,var(--gold-dark) 100%);
  position:relative;
}
.phone{
  position:absolute;width:226px;height:401px;border-radius:25px;overflow:hidden;
  background:var(--white);box-shadow:0 10px 22px rgba(60,40,10,.35);
}
.phone--splash{left:488px;top:191px}
.phone--landing{left:77px;top:705px}
.phone--login{left:350px;top:705px}
.phone--register{left:624px;top:705px}
.phone--home{left:897px;top:705px}
.nave-backdrop{
  position:absolute;inset:0;
  background:radial-gradient(ellipse at 50% 35%,#3b63ab 0%,var(--blue-top) 40%,var(--blue-bottom) 100%);
}
.wordmark{font-weight:500;color:var(--navy-text);letter-spacing:.3px;text-align:center;position:absolute;left:0;right:0}
.wordmark--light{color:var(--white);font-size:19px;top:219px}
.app-bar{position:absolute;left:0;right:0;top:0;height:35px;background:var(--header-blue)}
.app-bar svg{position:absolute;top:10px}
.field{
  position:absolute;height:26px;border:1px solid var(--field-border);border-radius:2px;
  font-size:7px;color:var(--grey-text);padding-left:9px;line-height:24px;background:var(--white);
}
.btn{
  position:absolute;height:27px;border-radius:2px;color:var(--white);
  background:linear-gradient(90deg,var(--btn-start),var(--btn-end));
  text-align:center;line-height:27px;
}
.field-label{position:absolute;font-size:7px;font-weight:500;color:var(--navy-text)}
.join-card{position:absolute;left:32px;top:87px;width:164px;height:225px;background:var(--white);border-radius:10px}
.fine{position:absolute;left:0;right:0;text-align:center;font-size:6px;color:#3c4048}
.fine a{color:var(--btn-start);text-decoration:none}
.icon-artwork{
  position:absolute;left:34px;top:186px;width:162px;height:215px;
  background:radial-gradient(circle at 50% 22%,#e6b865 0%,#c7893e 25%,#5a3b22 55%,#2c2a22 100%);
  border-radius:80px 80px 0 0;
}
.menu-item{position:absolute;width:64px;text-align:center;font-size:6.4px;line-height:7px;color:#4b4f58}
.menu-item svg{display:block;margin:0 auto 5px}
.menu-item--active{color:var(--gold-accent)}
.bottom-nav{position:absolute;left:0;right:0;top:372px;border-top:1px solid #e4e6ea;height:29px}
.bottom-nav svg{position:absolute;top:9px}
</style>
</head>
<body>

<!-- Splash -->
<section class="phone phone--splash">
  <div class="nave-backdrop" role="img" aria-label="Cathedral vaulted ceiling photograph in blue tint"></div>
  <div class="wordmark wordmark--light">PARISH APP</div>
</section>

<!-- Landing -->
<section class="phone phone--landing">
  <div class="nave-backdrop" role="img" aria-label="Cathedral vaulted ceiling photograph in blue tint"></div>
  <div class="join-card">
    <div class="wordmark" style="font-size:11px;top:66px">PARISH APP</div>
    <div class="field-label" style="left:16px;top:120px">Join an organization</div>
    <div class="field" style="left:16px;top:136px;width:132px">Enter code</div>
    <div class="btn" style="left:16px;top:167px;width:132px;font-size:7px">Register an organization</div>
  </div>
</section>

<!-- Login -->
<section class="phone phone--login">
  <div class="app-bar"></div>
  <div class="wordmark" style="font-size:11px;top:135px">PARISH APP</div>
  <div class="field" style="left:25px;top:184px;width:176px">Username</div>
  <div class="field" style="left:25px;top:216px;width:176px">Password</div>
  <div class="btn" style="left:25px;top:250px;width:176px;font-size:8.5px">Sign In</div>
  <div class="fine" style="top:291px">ForgotPassword? <a href="#">Click here</a></div>
  <div class="fine" style="top:307px">Dont have account? <a href="#">Create Account</a></div>
</section>

<!-- Registration -->
<section class="phone phone--register">
  <div class="app-bar">
    <svg style="left:14px" width="10" height="15" viewBox="0 0 10 15"><path d="M8 1.5 2 7.5l6 6" fill="none" stroke="#fff" stroke-width="1.6"/></svg>
  </div>
  <div class="field-label" style="left:24px;top:74px">Church name</div>
  <div class="field" style="left:24px;top:89px;width:176px">Enter name</div>
  <div class="btn" style="left:24px;top:123px;width:176px;font-size:8.5px">Register</div>
  <div class="fine" style="top:159px">$3.20 price/month &amp; free trial for X days</div>
  <div class="icon-artwork" role="img" aria-label="Religious icon painting with golden halo"></div>
</section>

<!-- Organization home -->
<section class="phone phone--home">
  <div class="app-bar">
    <svg style="left:14px" width="10" height="15" viewBox="0 0 10 15"><path d="M8 1.5 2 7.5l6 6" fill="none" stroke="#fff" stroke-width="1.6"/></svg>
    <svg style="right:14px;top:11px" width="15" height="13" viewBox="0 0 15 13"><path d="M0 1.5h15M0 6.5h15M0 11.5h15" stroke="#fff" stroke-width="1.6"/></svg>
  </div>

  <div class="menu-item" style="left:14px;top:100px">
    <svg width="20" height="20" viewBox="0 0 20 20" fill="none" stroke="#1f3a6e" stroke-width="1.1"><path d="M3 6c0 6 5 11 11 11l2-3-3-2-2 1.5C9 12 7.5 10.5 7 8.5L8.5 7 6.5 4 3 6Z"/><rect x="10" y="2" width="8" height="6" rx="1.5"/><path d="M12 5h.1M14 5h.1M16 5h.1"/></svg>
    Contact Us
  </div>
  <div class="menu-item menu-item--active" style="left:81px;top:100px">
    <svg width="20" height="20" viewBox="0 0 20 20" fill="none" stroke="#b8914c" stroke-width="1.1"><rect x="2" y="2" width="16" height="11" rx="1.5"/><path d="M8.5 5v5l4-2.5z"/><path d="M2 16h16"/><circle cx="7" cy="16" r="1"/></svg>
    Video List
  </div>
  <div class="menu-item" style="left:149px;top:100px">
    <svg width="20" height="20" viewBox="0 0 20 20" fill="none" stroke="#1f3a6e" stroke-width="1.1"><path d="M2 8v4M5 5v10M8 2v16M11 6v8M14 4v12M17 8v4"/></svg>
    Audio List
  </div>

  <div class="menu-item" style="left:14px;top:161px">
    <svg width="20" height="20" viewBox="0 0 20 20" fill="none" stroke="#1f3a6e" stroke-width="1.1"><path d="M14 9V2H4v16h6"/><path d="M7 6h5M7 9h5M7 12h3"/><path d="m12 17 1-3 4-4 2 2-4 4z"/></svg>
    Documents<br>List
  </div>
  <div class="menu-item" style="left:81px;top:161px">
    <svg width="20" height="20" viewBox="0 0 20 20" fill="none" stroke="#1f3a6e" stroke-width="1.1"><path d="M3 3h14v10H9l-4 3v-3H3z"/><path d="M7 7h6M7 10h6"/></svg>
    Message/<br>Chat Rooms
  </div>
  <div class="menu-item" style="left:149px;top:161px">
    <svg width="20" height="20" viewBox="0 0 20 20" fill="none" stroke="#1f3a6e" stroke-width="1.1"><rect x="2" y="2" width="16" height="16"/><path d="M2 2l16 16M18 2 10 10"/><path d="M6 15c-2-2-2-4 0-4s2 2 0 4Z"/></svg>
    Map/<br>Directions
  </div>

  <div class="menu-item" style="left:14px;top:224px">
    <svg width="20" height="20" viewBox="0 0 20 20" fill="none" stroke="#1f3a6e" stroke-width="1.1"><rect x="2" y="3" width="16" height="14"/><path d="M2 6h16M5 9h2v2H5zM5 13h2v2H5zM9 10h7M9 14h7"/></svg>
    Webpage
  </div>
  <div class="menu-item" style="left:81px;top:224px">
    <svg width="20" height="20" viewBox="0 0 20 20" fill="none" stroke="#1f3a6e" stroke-width="1.1"><path d="M10 1.5l2 2 3-.5.5 3 2 2-1.5 2.5 1 2.5-2.5 1.5-.5 3-3-.5-1 2-2-1.5-3 .5-.5-3L2 13l1-2.5L1.5 8l2-2 .5-3 3 .5z"/><circle cx="10" cy="8" r="2.5"/><path d="M6 14c1-2 7-2 8 0"/></svg>
    Profile<br>Settings
  </div>
  <div class="menu-item" style="left:149px;top:224px">
    <svg width="20" height="20" viewBox="0 0 20 20" fill="none" stroke="#1f3a6e" stroke-width="1.1"><path d="M10 1.5l2 2 3-.5.5 3 2 2-1.5 2.5 1 2.5-2.5 1.5-.5 3-3-.5-1 2-2-1.5-3 .5-.5-3L2 13l1-2.5L1.5 8l2-2 .5-3 3 .5z"/><circle cx="10" cy="10" r="4"/><path d="M10 8v2.5M10 12h.1"/></svg>
    Notification<br>Settings
  </div>

  <div class="menu-item" style="left:14px;top:286px">
    <svg width="20" height="20" viewBox="0 0 20 20" fill="none" stroke="#1f3a6e" stroke-width="1.1"><path d="M10 1.5l2 2 3-.5.5 3 2 2-1.5 2.5 1 2.5-2.5 1.5-.5 3-3-.5-1 2-2-1.5-3 .5-.5-3L2 13l1-2.5L1.5 8l2-2 .5-3 3 .5z"/><circle cx="10" cy="8" r="2"/><path d="M10 10v5M10 13h2"/></svg>
    Admin<br>Settings
  </div>
  <div class="menu-item" style="left:81px;top:286px">
    <svg width="20" height="20" viewBox="0 0 20 20" fill="none" stroke="#1f3a6e" stroke-width="1.1"><circle cx="10" cy="5" r="2.5"/><circle cx="4.5" cy="8" r="2"/><circle cx="15.5" cy="8" r="2"/><path d="M6 17v-4a4 4 0 0 1 8 0v4zM1.5 17v-3a3 3 0 0 1 4-2.5M18.5 17v-3a3 3 0 0 0-4-2.5"/></svg>
    Manage<br>members
  </div>
  <div class="menu-item" style="left:149px;top:286px">
    <svg width="20" height="20" viewBox="0 0 20 20" fill="none" stroke="#1f3a6e" stroke-width="1.1"><path d="M13 8V2H3v16h7"/><path d="M6 6h4M6 9h4M6 12h2"/><circle cx="14" cy="12" r="2"/><path d="M10.5 18c.5-2.5 6.5-2.5 7 0"/></svg>
    View Form<br>Submissions
  </div>

  <nav class="bottom-nav">
    <svg style="left:59px" width="12" height="12" viewBox="0 0 12 12" fill="none" stroke="#b9bcc3" stroke-width="1"><path d="M1 6 6 1.5 11 6v5H1z"/><path d="M4.5 11V8h3v3"/></svg>
    <svg style="left:109px" width="12" height="12" viewBox="0 0 12 12" fill="none" stroke="#b9bcc3" stroke-width="1"><path d="M2.5 9V5.5a3.5 3.5 0 0 1 7 0V9h1.5H1z"/><path d="M5 10.8h2"/></svg>
    <svg style="left:158px" width="12" height="12" viewBox="0 0 12 12" fill="none" stroke="#b9bcc3" stroke-width="1"><circle cx="6" cy="4" r="2.5"/><path d="M1.5 11.5a4.5 4.5 0 0 1 9 0z"/></svg>
  </nav>
</section>

</body>
</html>
```